Business Card Design

Business Card for professional consulting firm working with large financial institutions.

Target Market(s)

Executive buyers

Industry/Entity Type

Banking

Contact Information for Business Card

Mild creativity wanted. Not boring, but do elaborate artwork.

Font styles to use
Serif
Sans Serif

Colors

Designer to choose colors to be used in the design.

Requirements
Must have
• Standard business card features - company name, individual name, telephone, website, email, locations.
Nice to have
• Two colors
Should not have
• too many colors, fancy printing, cartoons.

```html
<!DOCTYPE html>
<html lang="en">
<head>
<meta charset="utf-8">
<title>k7advisory Business Card</title>
<link rel="stylesheet" href="https://fonts.googleapis.com/css2?family=Lora:wght@400&family=Roboto:wght@400&family=Roboto+Condensed:wght@500;700&display=swap">
<style>
  :root {
    --backdrop: #e8e4de;
    --card-light: #f4f4f4;
    --card-dark: #1b1c1e;
    --ink: #222222;
    --ink-soft: #3a3a3a;
    --muted: #9a9a9a;
    --rule: #b5b5b5;
    --white: #ffffff;
  }
  * { margin: 0; padding: 0; box-sizing: border-box; }
  html, body {
    width: 1200px; height: 960px; overflow: hidden;
    background: var(--backdrop);
  }
  .canvas { position: relative; width: 1200px; height: 960px; }
  .card { position: absolute; width: 600px; height: 343px; }
  .card-front { left: 314px; top: 113px; background: var(--card-light); }
  .card-back { left: 311px; top: 472px; background: var(--card-dark); }

  .wordmark {
    position: absolute;
    font-family: "Lora", Georgia, serif;
    font-weight: 400;
    white-space: nowrap;
  }
  .card-front .wordmark { right: 70px; top: 54px; font-size: 29px; color: var(--ink-soft); }
  .card-back .wordmark {
    left: 0; right: 0; top: 142px; text-align: center;
    font-size: 33px; color: var(--white);
  }

  .person-name {
    position: absolute; left: 32px; top: 200px;
    font-family: "Roboto Condensed", Arial, sans-serif;
    font-weight: 700; font-size: 22px; color: var(--ink); letter-spacing: 0.2px;
  }
  .person-title {
    position: absolute; left: 32px; top: 228px;
    font-family: "Roboto Condensed", Arial, sans-serif;
    font-weight: 500; font-size: 14px; color: var(--muted); letter-spacing: 0.3px;
  }
  .title-rule {
    position: absolute; left: 151px; right: 34px; top: 236px;
    height: 1px; background: var(--rule);
  }

  .contact-list {
    position: absolute; left: 32px; top: 262px; list-style: none;
    font-family: "Roboto", Arial, sans-serif; font-size: 14px; color: var(--ink-soft);
  }
  .contact-list li { display: flex; align-items: center; height: 19px; }
  .contact-list svg { width: 13px; height: 13px; margin-right: 8px; fill: var(--ink); }

  .address {
    position: absolute; right: 32px; top: 262px; text-align: right;
    font-family: "Roboto", Arial, sans-serif; font-size: 14px; line-height: 19px;
    color: var(--ink-soft); font-style: normal;
  }
</style>
</head>
<body>
<main class="canvas">
  <section class="card card-front" aria-label="Card front">
    <div class="wordmark">k7advisory</div>

    <h1 class="person-name">DANIEL REYES</h1>
    <p class="person-title">CEO/FOUNDER</p>
    <div class="title-rule"></div>

    <ul class="contact-list">
      <li>
        <svg viewBox="0 0 16 16" aria-hidden="true"><path d="M3.6 1.2l2.3 2.6c.4.4.4 1 0 1.4L4.7 6.5c.9 2 2.6 3.7 4.7 4.7l1.3-1.2c.4-.4 1-.4 1.4 0l2.6 2.3c.4.4.4 1 0 1.4l-1.2 1.2c-.6.6-1.5.8-2.3.5C6.6 13.9 2.1 9.4.6 4.8.3 4 .5 3.1 1.1 2.5l1.1-1.3c.4-.4 1-.4 1.4 0z"/></svg>
        555 210 4817
      </li>
      <li>
        <svg viewBox="0 0 16 16" aria-hidden="true"><path d="M1 3h14v1.2L8 9 1 4.2z"/><path d="M1 5.6l7 4.8 7-4.8V13H1z"/></svg>
        info@k7advisory.com
      </li>
      <li>
        <svg viewBox="0 0 16 16" aria-hidden="true"><circle cx="8" cy="8" r="7"/><path d="M5 4.5c1 .3 1.6 1 1.4 2-.2.8-1.4 1-1.2 2 .2 1.1 1.5 1 1.5 2.4 0 .7-.3 1.4-.5 2" stroke="#f4f4f4" stroke-width="1.3" fill="none"/><path d="M10.5 3.5c-.6 1 .2 1.7 1.2 2 .9.3.8 1.5.3 2.3" stroke="#f4f4f4" stroke-width="1.3" fill="none"/></svg>
        www.k7advisory.com
      </li>
    </ul>

    <address class="address">
      k7advisory<br>
      1420 Harbor Street<br>
      Juneau, Alaska 99801
    </address>
  </section>

  <section class="card card-back" aria-label="Card back">
    <div class="wordmark">k7advisory</div>
  </section>
</main>
</body>
</html>
```